FREE BBQ for life if you win our business with your creative menu design

Looking for a 11x17 size menu. we are a full service BBQ restaurant. We have an upscale environment as well as up scale service. We offer 5 star dinning at a casual price. we are on route 84 and are proud of that. we offer the finest smoked meats. Specializing in smoked pork beef and bison. we have an old barn wood decor. we only use oak to smoke our meats. use a lot of tarnished metal as well as some string nail art. Looking for a menu that goes along our style. i have attached as many pictures as i could to give you a fill of how we do it out here.
PLEASE USE THE 11"X17" MENU TEMPLATE ATTACHED IN THE PROJECT BRIEF.
Target Market(s)
Cool people and there families.
Industry/Entity Type
Business
Requirements
Must have
- I have attached the Current menu we use. File brantlys menu pub. Those are all the Items. There will be some changes as we but together the new menu. The prices are changing. but that should be an easy change as we go.
Nice to have
- We are getting away from the lunch dinner menu and going to an all day menu. so rather than coming with toast or bun we will now be asking as an option. I have attached a menu i tried to make as a sample of how we will be doing it. new menu single page and new menu single page flame. These are ideas i had but could not really make it work. so use them as an idea of what we are looking for but be creative.

```html
<!DOCTYPE html>
<html lang="en">
<head>
<meta charset="utf-8">
<title>Brantlys Barbeque Menu</title>
<link href="https://fonts.googleapis.com/css2?family=Arimo:wght@400;700&family=Zilla+Slab:wght@700&display=swap" rel="stylesheet">
<style>
:root{
  --page:#e6e3de;
  --red:#e1252b;
  --ink:#1c1410;
  --wood:#3b2417;
  --wood-dark:#24150d;
  --parch:#ecd7ab;
  --parch-edge:#d6b073;
  --blue:#24479b;
  --flame-a:#f7b32b;
  --flame-b:#d9401b;
  --photo-a:#5a2a22;
  --photo-b:#0f0c0b;
}
*{margin:0;padding:0;box-sizing:border-box}
html,body{width:866px;height:1200px;overflow:hidden;background:var(--page)}
.menu{position:absolute;left:43px;top:0;width:836px;height:1286px;transform:scale(.9331);transform-origin:0 0;
  font-family:"Arimo",Arial,sans-serif;color:var(--ink);background:linear-gradient(180deg,var(--wood),var(--wood-dark));}
.header{position:absolute;left:0;top:0;width:836px;height:151px}
.brand{position:absolute;left:0;top:0;width:373px;height:151px;background:radial-gradient(ellipse at 50% 30%,var(--flame-a),var(--flame-b) 80%);
  display:flex;flex-direction:column;align-items:center;justify-content:center;gap:6px}
.brand-name{font-family:"Arimo",Arial,sans-serif;font-weight:700;font-size:30px;color:var(--blue);letter-spacing:1px;display:flex;align-items:center;gap:10px}
.brand-mark{width:22px;height:22px;border-radius:50%;background:var(--blue)}
.brand-phone{font-weight:700;font-size:14px;color:var(--wood-dark)}
.photo{position:absolute;left:373px;top:0;width:463px;height:151px;background:radial-gradient(ellipse at 55% 60%,var(--photo-a),var(--photo-b) 75%)}
.parchment{position:absolute;left:24px;top:156px;width:776px;height:1072px;border-radius:6px;
  background:radial-gradient(ellipse at 50% 45%,var(--parch) 55%,var(--parch-edge));}
.col{position:absolute;width:310px}
.section-title{font-family:"Zilla Slab",Georgia,serif;font-weight:700;font-size:50px;line-height:44px;color:var(--red);letter-spacing:1px;
  text-shadow:-1px -1px 0 #fff,1px -1px 0 #fff,-1px 1px 0 #fff,1px 1px 0 #fff,2px 2px 2px rgba(0,0,0,.25)}
.title-row{display:flex;align-items:center;gap:12px;margin-bottom:14px}
.tag{font-weight:700;font-size:12px;color:var(--red)}
.tag.blue{color:var(--blue)}
.chef{width:64px;height:68px;border-radius:50%;background:radial-gradient(circle,#f2a36b,#c8472c)}
.gf{width:30px;height:30px;border-radius:50%;background:var(--blue)}
.item{margin-bottom:13px}
.item h3{font-size:14px;line-height:17px;font-weight:700}
.item h3 .price,.price{color:var(--red);font-weight:400}
.item h3 small{font-size:11px}
.item p{font-size:9.5px;line-height:12.5px}
.note{font-size:12px;font-weight:700;line-height:15px;position:relative}
.note::before{content:"*";position:absolute;left:-15px}
.note.red{color:var(--red)}
.note.red::before{content:"* *";left:-28px}
.sides{display:grid;grid-template-columns:202px 1fr;font-size:13.5px;font-weight:700;line-height:17.5px}
.drink-row{display:flex;justify-content:space-between;align-items:flex-start}
.badge{width:50px;height:18px;background:var(--blue);margin-top:2px}
.badge.maroon{background:#8b1c24}
.hot{display:grid;grid-template-columns:1fr 1fr 1fr;font-size:13.5px;font-weight:700;text-align:center;line-height:17px}
.hot .price{font-weight:700}
.footer{position:absolute;left:437px;top:1232px;display:flex;align-items:center;gap:10px;color:#fff;font-size:11.5px;font-weight:700;line-height:15px}
.footer-name{font-size:20px;font-weight:700;color:#3ba9d9}
</style>
</head>
<body>
<div class="menu">
  <header class="header">
    <div class="brand">
      <div class="brand-name"><span class="brand-mark"></span>BRANTLYS BARBEQUE</div>
      <div class="brand-phone">505-555-0148</div>
    </div>
    <div class="photo" role="img" aria-label="Photo of smoked brisket being sliced with a knife"></div>
  </header>
  <div class="parchment"></div>

  <section class="col" style="left:89px;top:182px">
    <div class="title-row"><h2 class="section-title">BISON</h2><div class="chef" role="img" aria-label="Cartoon chef illustration"></div><span class="tag">Heart Healthy</span></div>
  </section>
  <section class="col" style="left:89px;top:246px">
    <div class="item"><h3>Bison Brisket - <span class="price">18.65</span></h3><p>The belly of beast, smoked then sliced thin and grilled. Juicy and tender</p></div>
    <div class="item"><h3>Bison Burger - <span class="price">12.59</span></h3><p>Smoked then grilled served with pepper jack cheese lettuce tomato pickle toped with spicy ranch.</p></div>
    <div class="item"><h3>Bison Steak - <span class="price">34.56</span></h3><p>12oz of lean healthy meat cooked to your desired temp.</p></div>
    <p class="note" style="margin-top:16px">Served with 1 sides and your choice of Texas toast, Kaiser bun, or Glutton Free bread</p>
  </section>

  <section class="col" style="left:89px;top:450px">
    <div class="title-row"><h2 class="section-title">SMOKED</h2><span class="gf"></span><span class="tag blue">Glutton free</span></div>
    <div class="item"><h3>Baby Back Ribs - <small>Full Rack <span class="price">22.59</span> - Half Rack <span class="price">12.49</span></small></h3><p>Tender to the bone, finger licking good, never need a knife, best ribs you'll ever have.</p></div>
    <div class="item"><h3>St. Louis Ribs - <small>Half <span class="price">16.45</span> - Full <span class="price">30.89</span></small></h3><p>A nice big tender rib , slow smoked, so tender that you can sink your teeth into.</p></div>
    <div class="item"><h3>Beef Brisket - <span class="price">10.95</span></h3><p>The most insane mouth watering smoky, moist, succulent piece of meat your mouth will ever have.</p></div>
    <div class="item"><h3>Pulled Pork - <span class="price">9.59</span></h3><p>Smoked for 18-20 hrs. then pulled and mixed with our signature base barbeque sauce .</p></div>
    <div class="item"><h3>Sliced Pork - <span class="price">10.54</span></h3><p>Smoked juicy tenderloin sliced thin then grilled per order .</p></div>
    <div class="item"><h3>Smoked Turkey - <span class="price">11.49</span></h3><p>Breast meat smoked and sliced. Juicy and tender .</p></div>
    <div class="item"><h3>Smoked Chicken half - <span class="price">13.59</span></h3><p>Moist and juicy smoked Breast and thigh on the bone basted with our signature sauce on the grill.</p></div>
    <div class="item"><h3>Rib Eye - <span class="price">21.95</span></h3><p>12oz juicy steak grilled to your desired temp</p></div>
    <p class="note" style="margin-top:16px">Served with 1 sides and your choice of Texas toast, Kaiser bun, or Glutton Free bread</p>
    <p class="note red" style="margin-top:6px">All meats are Glutton free Please specify if you are glutton Intolerant.</p>
  </section>

  <section class="col" style="left:89px;top:1003px">
    <h2 class="section-title" style="margin-bottom:16px">SALADS</h2>
    <div class="item" style="margin-bottom:18px"><h3>All you can eat salad bar - <span class="price">7.89</span></h3><p>Enjoy as much salad as you would like</p></div>
    <div class="item" style="margin-bottom:12px"><h3>Meaty Salad - <span class="price">3.00</span></h3><p>Choose any meat to add to your salad 3oz of meat .<br>(Excludes ribs and bison.)</p></div>
    <div class="item"><h3>Side Salad - <small>With out meal <span class="price">3.00</span> - Add to meal <span class="price">1.50</span></small></h3></div>
  </section>

  <section class="col" style="left:448px;top:186px;width:304px">
    <h2 class="section-title" style="margin-bottom:16px">APPETIZERS</h2>
    <div class="item"><h3>King Rings - <span class="price">7.89</span></h3><p>Green Chili battered fried golden crispy 1" thick onion rings. Served with spicy ranch.</p></div>
    <div class="item"><h3>Deep Fried Pickles - <span class="price">7.89</span></h3><p>Crisp dill pickle chips battered and fried to a golden crispy brown. Served with spicy ranch.</p></div>
    <div class="item"><h3>Fried Okra - <span class="price">7.89</span></h3><p>Okra is breaded then fried until golden. Served with spicy ranch.</p></div>
    <div class="item"><h3>Green Chili Waffle Fries - <span class="price">7.89</span></h3><p>Crispy waffle-cut Fries, topped with a savory blend of cheese, and New Mexico green chile. Served with spicy ranch.</p></div>
    <div class="item" style="margin-bottom:18px"><h3>BB Wild Wings - <span class="price">9.99</span></h3><p>Big, meaty pork wings, deep fried to a perfect golden brown, tossed in a hot Buffalo-style sauce, and served with spicy buttermilk ranch dressing on the side. Served with spicy ranch.</p></div>
    <div class="item"><h3>Sampler Platter - <span class="price">8.99</span></h3><p>Two BB Wild Wings, 6oz of Fried Pickles, 6oz of King Rings. Served with spicy ranch.</p></div>

    <h2 class="section-title" style="margin:26px 0 14px">SIDES</h2>
    <div class="sides">
      <span>*Green Chile Creamed Corn</span><span></span>
      <span>*Potato Salad</span><span>*Baked Beans</span>
      <span>*Baked Potato</span><span>*Waffle Fries</span>
      <span>*Grilled Veggies</span><span>*Coleslaw</span>
    </div>
    <p class="tag" style="font-size:13px;margin-top:16px">**Extra side 2.29</p>

    <h2 class="section-title" style="margin:26px 0 16px">DESSERTS</h2>
    <div class="item" style="margin-bottom:16px"><h3>Peach Cobbler <span class="price">&amp;</span> Ice Cream - <small>large <span class="price">5.89</span> Small <span class="price">3.29</span></small></h3><p>Served hot topped with ice cream.</p></div>
    <div class="item"><h3>Cookies A-L-Mode - <small>large <span class="price">5.89</span> Small <span class="price">3.29</span></small></h3><p>Hot gooey cookies topped with ice cream your choice chocolate chip or macadamia nut. large 5.89 Small</p></div>
    <p class="note" style="font-size:11.5px;margin-top:16px">Dessert of the week<br><span style="color:var(--red)">Ask your server for our special dessert of the week</span></p>

    <h2 class="section-title" style="margin:24px 0 14px">DRINKS</h2>
    <div class="drink-row item"><div><h3>Lemonade - <span class="price">2.59</span></h3><p>Regular, Strawberry, Watermelon, Cherry, Peach</p></div><span class="badge"></span></div>
    <div class="drink-row item"><div><h3>Fountain - <span class="price">1.89</span></h3><p>Cola, Pepper Soda , Root Beer , Lemon Lime, Citrus Kick , Diet Cola<br>Diet Pepper Soda</p></div><span class="badge maroon" style="margin-top:-18px"></span></div>
    <div class="hot" style="margin-top:8px">
      <span>Iced Teas<br><span class="price">1.89</span></span>
      <span>Coffee<br><span class="price">2.69</span></span>
      <span>Hot Chocolate<br><span class="price">2.89</span></span>
    </div>
  </section>

  <footer class="footer">
    <span class="footer-name">Loyly</span>
    <span>Join our Customer loyalty app.<br>Get free food when you become a loyal customer.</span>
  </footer>
</div>
</body>
</html>
```